NZ First of it's kind solutions directory and marketplace for busy Mums needs a business card design

We need a business card design for our new nationwide business in NZ (long term plans to go global). We provide solutions to the everyday challenges that busy Mums face by connecting them with quality communities and suppliers of carefully selected, relevant products and services. We sell direct via our online marketplace. The final design should communicate our values of inclusivity, quality and smart solutions. Colours should incorporate our logo colour palette of #477077 and #6ba8b2. Our website is at https://www.brightnestmums.example

Target Market(s)

busy Mums, Age 28 – 50, female, income over $100K, location main centres NZ primarily but NZ wide. Is likely juggling work or career with a young family. Probably had hobbies which have fallen by the wayside.
-Wants to succeed in her chosen career without compromising on family life
-to successfully juggle her career without feeling like she is compromising her children
- Is time poor, something always has to give and it’s generally her health (she’ll stay up late, get stressed)
- probably ex corporate or professional career. Has discretional income

Industry/Entity Type

Business

Contact Information for Business Card

Lena Forbisher, Founder, BrightNestMums.example (Strapline Tap; Gather; Sorted), 47 Kowhai Terrace, Ellerslie, Auckland 1051, New Zealand. Mob: 021 483 517 Ph: +64 (0)9 571 4860

Font styles to use
Other font styles liked:
• Raleway, and/or Architects Daughter

Colors
00a990
33b8a4
86cfc6
cfeae6

Requirements
Must have
• the above details, streamline. the logo and colours associated with those logos
Should not have
• foil or metallic colours

```html
<!DOCTYPE html>
<html lang="en">
<head>
<meta charset="utf-8">
<title>BrightNestMums – Business Card</title>
<link rel="stylesheet" href="https://fonts.googleapis.com/css2?family=Raleway:wght@400;500;700;800&family=Architects+Daughter&display=swap">
<style>
  :root {
    --teal-deep: #477077;
    --teal-light: #6ba8b2;
    --ink: #3d4a4d;
    --paper: #ffffff;
    --paper-tint: #f7f9f9;
    --backdrop: #e6e9ea;
  }
  * { box-sizing: border-box; margin: 0; padding: 0; }
  html, body {
    width: 1200px; height: 900px; overflow: hidden;
    background: var(--backdrop);
    font-family: "Raleway", Arial, sans-serif;
    color: var(--ink);
  }
  .canvas {
    position: relative; width: 1200px; height: 900px;
  }
  .card {
    position: absolute; left: 240px;
    width: 720px; height: 410px;
    background: var(--paper);
    box-shadow: 0 10px 28px rgba(0,0,0,0.18);
    overflow: hidden;
  }
  /* Front */
  .card--front { top: 30px; display: flex; }
  .front-panel {
    width: 40%; height: 100%;
    background: var(--teal-deep);
    display: flex; align-items: center; justify-content: center;
  }
  .front-panel .brand-disc {
    width: 150px; height: 150px; border-radius: 50%;
    background: var(--paper);
  }
  .front-main {
    flex: 1; display: flex; flex-direction: column;
    align-items: center; justify-content: center; gap: 14px;
    padding: 0 40px 40px;
  }
  .front-wordmark {
    font-weight: 800; font-size: 28px; letter-spacing: -0.3px;
    color: var(--teal-deep); white-space: nowrap;
  }
  .front-url {
    font-family: "Architects Daughter", cursive;
    font-size: 17px; color: var(--ink); white-space: nowrap;
  }
  /* Back */
  .card--back { top: 460px; background: var(--paper-tint); }
  .edge-band {
    position: absolute; left: 0; top: 118px; bottom: 0; width: 14px;
    background: var(--teal-light);
  }
  .edge-band::after {
    content: ""; position: absolute; left: 0; right: 0; top: 130px; bottom: 0;
    background: var(--teal-deep);
  }
  .back-brand {
    position: absolute; left: 42px; top: 104px;
  }
  .back-wordmark {
    font-weight: 800; font-size: 36px; letter-spacing: -0.5px;
    color: var(--teal-deep);
  }
  .strapline {
    font-family: "Architects Daughter", cursive;
    font-size: 16px; color: var(--teal-light); margin-top: 2px;
  }
  .person { position: absolute; left: 42px; top: 222px; }
  .person-name {
    font-weight: 800; font-size: 19px; text-transform: uppercase; color: var(--teal-deep);
  }
  .person-name .surname { color: var(--teal-light); }
  .person-role { font-size: 16px; color: var(--ink); margin-top: 1px; }
  .contact-list {
    position: absolute; left: 42px; top: 298px; list-style: none;
    font-size: 16px; line-height: 26px; color: var(--ink);
  }
  .contact-list li { display: flex; align-items: center; gap: 12px; }
  .contact-list svg { width: 15px; height: 15px; fill: var(--teal-deep); }
  .address-block {
    position: absolute; right: 40px; top: 70px;
    display: flex; flex-direction: column; align-items: flex-end;
  }
  .address-block .brand-disc {
    width: 72px; height: 72px; border-radius: 50%;
    background: var(--teal-deep); margin-right: 40px; margin-bottom: 26px;
  }
  .address { font-size: 16px; line-height: 21px; text-align: right; }
</style>
</head>
<body>
<main class="canvas">
  <section class="card card--front" aria-label="Business card front">
    <div class="front-panel"><span class="brand-disc"></span></div>
    <div class="front-main">
      <p class="front-wordmark">BrightNestMums.example</p>
      <p class="front-url">www.brightnestmums.example</p>
    </div>
  </section>

  <section class="card card--back" aria-label="Business card back">
    <span class="edge-band"></span>
    <div class="back-brand">
      <p class="back-wordmark">BrightNestMums</p>
      <p class="strapline">Strapline Tap; Gather; Sorted</p>
    </div>
    <div class="person">
      <p class="person-name">Lena <span class="surname">Forbisher</span></p>
      <p class="person-role">Founder</p>
    </div>
    <ul class="contact-list">
      <li>
        <svg viewBox="0 0 24 24" aria-hidden="true"><path d="M6.6 10.8a15.1 15.1 0 0 0 6.6 6.6l2.2-2.2a1 1 0 0 1 1-.25 11.4 11.4 0 0 0 3.6.57 1 1 0 0 1 1 1V20a1 1 0 0 1-1 1A17 17 0 0 1 3 4a1 1 0 0 1 1-1h3.5a1 1 0 0 1 1 1c0 1.250.2 2.450.57 3.57a1 1 0 0 1-.25 1z"/></svg>
        +64 (0)9 571 4860
      </li>
      <li>
        <svg viewBox="0 0 24 24" aria-hidden="true"><path d="M7 1h10a2 2 0 0 1 2 2v18a2 2 0 0 1-2 2H7a2 2 0 0 1-2-2V3a2 2 0 0 1 2-2zm0 3v14h10V4zm5 15.2a1 1 0 1 0 0 2 1 1 0 0 0 0-2z"/></svg>
        +64 021 483 517
      </li>
      <li>
        <svg viewBox="0 0 24 24" aria-hidden="true"><path d="M2 5h20v14H2zm2 2v.4l8 5.2 8-5.2V7zm0 2.8V17h16V9.8l-8 5.2z"/></svg>
        hello@brightnestmums.example
      </li>
    </ul>
    <div class="address-block">
      <span class="brand-disc"></span>
      <p class="address">47 Kowhai Terrace, Ellerslie<br>Auckland 1051, NZ.</p>
    </div>
  </section>
</main>
</body>
</html>
```